Packaging Design for Vanta Prime

We require an outstanding packaging design for our Vanta Prime brand, which offers hydration electrolyte supplements specifically tailored for athletes and sporty individuals.

Benchmark packaging design from quellix competitor attached. The product packaging contains 20 x 20g sticks of the product.

Target Market

Psychographic: Health-conscious, active lifestyle, values quality, functionality and sustainability.

product description 1:
HYDRATION BOOSTER
Refresh, Replenish, Recharge!

product description 2:
PREMIUM ISOTONIC ELECTROLYTE DRINK
Nutritional Expertise Since 1992.

Existing Logo: to add "since 1992"

Appeal to Target Market: Create a design that resonates with both men and women in the 25-55 age group.

Grafik Design: Develop a visually striking design that grabs attention in online retail environments like Brindleport.

Visuals: glass of water (or symbolic) and sticks (powder) just like benchmark brand quellix.

Design Elements
Use colours that are inside the Vanta-Prime Logo, attached.
Product will be available in 3 flavours. Lemon=yellow, Orange=orange, Black Currant=purple

Typography: Utilize strong, clean, and modern fonts. Ensure readability and create a sense of strength, endurance and reliability.

The product will be available in 3 flavours: Lemon, Orange and Johannisbeere

We look forward to seeing your creative ideas and innovative designs for our Vanta Prime brand packaging.

```html
<!DOCTYPE html>
<html lang="en">
<head>
<meta charset="UTF-8">
<title>Vanta Prime – Hydration Booster Lemon</title>
<link href="https://fonts.googleapis.com/css2?family=Archivo:wght@700;800&family=Saira:wght@400;500&display=swap" rel="stylesheet">
<style>
  :root {
    --backdrop: #f7ec6b;
    --pouch: #ffffff;
    --lemon: #f2e01c;
    --magenta: #c41a6c;
    --pink-soft: #e79cc5;
    --pink-pale: #eab2d0;
    --glass: #e9eeef;
    --zip: #e6e6e6;
  }
  * { margin: 0; padding: 0; box-sizing: border-box; }
  html, body {
    width: 1200px; height: 972px; overflow: hidden;
    background: var(--backdrop);
    font-family: "Archivo", Arial, sans-serif;
  }
  .pouch {
    position: absolute; left: 300px; top: 152px;
    width: 600px; height: 668px;
    background: var(--pouch);
    border-radius: 14px;
    overflow: hidden;
  }
  .zip-line {
    position: absolute; left: 29px; top: 61px;
    width: 541px; height: 2px;
    background: var(--zip);
    z-index: 1;
  }
  .count-tab {
    position: absolute; left: 36px; top: 0;
    width: 71px; height: 95px;
    background: var(--lemon);
    color: var(--magenta);
    text-align: center;
    padding-top: 32px;
    z-index: 2;
  }
  .count-tab .count-number { display: block; font-size: 34px; font-weight: 800; line-height: 1; }
  .count-tab .count-label { display: block; font-size: 13px; font-weight: 700; line-height: 1.1; margin-top: 3px; }
  .brand {
    position: absolute; left: 62px; top: 150px;
    display: flex; align-items: center; gap: 14px;
  }
  .brand-dot {
    width: 40px; height: 40px; border-radius: 50%;
    background: var(--magenta);
  }
  .brand-name {
    font-size: 66px; font-weight: 800; color: var(--magenta);
    letter-spacing: -1px; line-height: 1;
  }
  .since {
    position: absolute; left: 360px; top: 232px;
    font-family: "Saira", Arial, sans-serif;
    font-size: 20px; font-weight: 500; color: var(--magenta);
  }
  .stick-visual {
    position: absolute; left: 155px; top: 300px;
    width: 280px; height: 62px;
    transform: rotate(-14deg);
    background: linear-gradient(90deg, #f3dbe7 0%, #ffffff 12%, #f8f8f8 80%, var(--lemon) 86%);
    border: 1px solid #eee;
  }
  .glass-visual {
    position: absolute; left: 67px; top: 360px;
    width: 148px; height: 308px;
    background: linear-gradient(180deg, rgba(220,225,228,0.35) 0%, var(--glass) 28%, #f1e07a 58%, #e9b83a 66%, var(--glass) 80%, #e2e6e8 100%);
    border-radius: 6px 6px 0 0;
  }
  .band {
    position: absolute; left: 0; bottom: 0; width: 600px; height: 101px;
  }
  .band polygon { fill: var(--lemon); }
  .product-name {
    position: absolute; right: 55px; top: 385px;
    text-align: right; color: var(--magenta);
    font-size: 40px; font-weight: 800; line-height: 0.98;
    letter-spacing: -0.5px;
  }
  .tagline {
    position: absolute; right: 55px; top: 466px;
    font-family: "Saira", Arial, sans-serif;
    font-size: 18px; color: var(--magenta);
  }
  .descriptor {
    position: absolute; right: 55px; top: 496px;
    text-align: right; color: var(--pink-soft);
    font-size: 23px; font-weight: 700; line-height: 1;
  }
  .expertise {
    position: absolute; right: 55px; top: 550px;
    font-family: "Saira", Arial, sans-serif;
    font-size: 13px; color: var(--pink-pale);
  }
  .flavour {
    position: absolute; left: 225px; top: 606px;
    font-size: 25px; font-weight: 800; color: var(--magenta);
  }
  .net-content {
    position: absolute; right: 55px; top: 611px;
    font-family: "Saira", Arial, sans-serif;
    font-size: 16px; color: var(--magenta);
  }
</style>
</head>
<body>
  <main class="pouch">
    <div class="zip-line"></div>
    <div class="count-tab">
      <span class="count-number">20</span>
      <span class="count-label">STICKS</span>
    </div>

    <div class="brand">
      <span class="brand-dot"></span>
      <span class="brand-name">Vanta Prime</span>
    </div>
    <p class="since">since 1992</p>

    <div class="stick-visual" role="img" aria-label="Single product stick pouring powder"></div>

    <svg class="band" viewBox="0 0 600 101" preserveAspectRatio="none" aria-hidden="true">
      <polygon points="0,0 600,47 600,101 0,101"/>
    </svg>

    <div class="glass-visual" role="img" aria-label="Glass of sparkling water with a lemon slice and falling powder"></div>

    <h1 class="product-name">HYDRATION<br>BOOSTER</h1>
    <p class="tagline">Refresh, Replenish, Recharge!</p>
    <p class="descriptor">PREMIUM ISOTONIC<br>ELECTROLYTE DRINK</p>
    <p class="expertise">Nutritional Expertise Since 1992</p>

    <p class="flavour">LEMON</p>
    <p class="net-content">20 x 20g sticks</p>
  </main>
</body>
</html>
```